Camp Thornbrook 2021 Magazine Design

We are for someone to design our annual magazine/newsletter. This is a print newsletter that is a total of 20 pages. It will need to be designed in a way that is easy to share with our printers. The designer will need to be someone who is creative and easy to work with.
For those interested in this project we ask that you design 4 to 6 pages for us to view. Once we select the designer we will want the rest created in a two-week time span. For those submitting a bid please include front cover, theme & dates, mission & vision, and Make the Difference.

This link will provide the layout of the newsletter https://files.parcelvault.example/doc/7qzRk2LmVt9XwPa4NbHc6DsYe3FuJg8KoTiW5rQx/edit?share=1.

This link will provide you with the pictures that are needed and a few documents https://files.parcelvault.example/folders/4TpWx8QnRb2ZyLc7MfVd5HsJ?share=1

Details:
20 pages long (including covers)
8.5 x 11

Please message me if you need any further details.

Target Market(s)

Our alumni base. Covers all ages

Requirements
Must have
• Spelled out in document
Nice to have
• Spelled out in document
Should not have
• Spelled out in document

```html
<!DOCTYPE html>
<html lang="en">
<head>
<meta charset="utf-8">
<title>Camp Thornbrook 2021 Magazine – Contents &amp; Make the Difference</title>
<link rel="stylesheet" href="https://fonts.googleapis.com/css2?family=Bebas+Neue&family=Open+Sans:wght@400;600&display=swap">
<style>
  :root {
    --ink: #1e1e1e;
    --heading: #4a4032;
    --orange: #f29b5c;
    --teal: #4e9e98;
    --forest: #242b26;
    --leaf: #6f8d4f;
    --bark: #7a6548;
    --muted: #555;
    --rule: #c9c9c9;
  }
  * { box-sizing: border-box; margin: 0; padding: 0; }
  html, body { width: 1200px; height: 1000px; overflow: hidden; background: #fff; }
  body { position: relative; font-family: "Open Sans", sans-serif; color: var(--ink); }

  .page {
    position: absolute; top: 124px; width: 556px; height: 719px;
    border: 1px solid var(--rule); overflow: hidden; background: #fff;
  }
  .page--contents { left: 36px; }
  .page--feature { left: 608px; }

  /* Contents page */
  .hero-photo {
    position: absolute; left: 0; top: 0; width: 360px; height: 600px;
    background:
      linear-gradient(90deg, rgba(255,255,255,0) 55%, #fff 92%),
      linear-gradient(180deg, #4f6d3f 0%, #7f9860 40%, #8a7a5a 70%, #a09a6a 100%);
  }
  .hero-photo::after {
    content: ""; position: absolute; left: 30px; top: 90px; width: 160px; height: 510px;
    background: linear-gradient(90deg, #6a5a44, var(--bark) 50%, #5d4d39);
    opacity: .85;
  }
  .forest-band {
    position: absolute; left: 0; bottom: 0; width: 100%; height: 190px;
    background: linear-gradient(180deg, rgba(36,43,38,0) 0%, var(--forest) 30%, var(--forest) 100%);
  }

  .contents {
    position: absolute; left: 316px; top: 112px; width: 206px;
  }
  .contents__title {
    font-family: "Bebas Neue", sans-serif; font-size: 33px; line-height: 1;
    color: var(--heading); letter-spacing: .2px; margin-bottom: 14px;
  }
  .contents__list { list-style: none; }
  .contents__item {
    display: flex; justify-content: space-between; align-items: flex-end;
    font-size: 11.5px; line-height: 14px; height: 29.5px;
  }
  .contents__item--tall { height: 43px; }
  .contents__page { font-weight: 600; }
  .is-orange { color: var(--orange); }
  .is-teal { color: var(--teal); }

  .brand-mark {
    position: absolute; left: 444px; top: 622px; width: 84px;
    display: flex; flex-direction: column; align-items: center; gap: 4px;
  }
  .brand-mark__dot { width: 34px; height: 34px; border-radius: 50%; background: var(--orange); }
  .brand-mark__name { font-size: 10px; font-weight: 600; color: #fff; white-space: nowrap; }

  /* Feature page */
  .feature-header {
    position: absolute; left: 33px; right: 32px; top: 36px;
    display: flex; justify-content: space-between; align-items: baseline;
  }
  .feature-header__title {
    font-family: "Bebas Neue", sans-serif; font-size: 22px; color: var(--heading); line-height: 1;
  }
  .feature-header__url { font-size: 11px; color: var(--muted); }
  .feature-rule { position: absolute; left: 0; right: 0; top: 72px; height: 4px; background: var(--orange); }

  .story {
    position: absolute; top: 124px; font-size: 10.2px; line-height: 12px; color: var(--ink);
  }
  .story p + p { margin-top: 12px; }
  .story--left { left: 33px; width: 240px; }
  .story--right { left: 284px; width: 242px; }

  .zigzag-band {
    position: absolute; left: 284px; top: 243px; width: 239px; height: 17px;
    background: var(--teal); opacity: .9;
  }
  .campaign-photo {
    position: absolute; left: 281px; top: 281px; width: 242px; height: 364px;
    background: linear-gradient(180deg, #5f8a3e 0%, #88a86a 35%, #8f9aa0 65%, #6f7f8c 100%);
  }

  .folio-bar { position: absolute; right: 0; top: 689px; width: 57px; height: 4px; background: var(--orange); }
  .folio { position: absolute; right: 33px; top: 698px; font-family: "Bebas Neue", sans-serif; font-size: 15px; color: var(--heading); }
</style>
</head>
<body>

<section class="page page--contents">
  <div class="hero-photo" role="img" aria-label="Photo of a carved tree stump with a cross cut into it, in a wooded camp clearing"></div>
  <div class="forest-band" role="img" aria-label="Dark pine forest silhouette along the bottom of the page"></div>

  <nav class="contents">
    <h1 class="contents__title">Table of Contents</h1>
    <ol class="contents__list">
      <li class="contents__item"><span>Make the Difference</span><span class="contents__page is-orange">3</span></li>
      <li class="contents__item"><span>Golf Tournament</span><span class="contents__page is-teal">4 - 5</span></li>
      <li class="contents__item"><span>2021 Theme and Dates</span><span class="contents__page is-orange">6 - 7</span></li>
      <li class="contents__item contents__item--tall"><span>Where Are They Now:<br>Casey Holloway</span><span class="contents__page is-teal">8 - 9</span></li>
      <li class="contents__item"><span>2019 Donors</span><span class="contents__page is-orange">10 - 12</span></li>
      <li class="contents__item"><span>2019 Thornbrook Awards</span><span class="contents__page is-teal">13</span></li>
      <li class="contents__item"><span>Hawk Ridge</span><span class="contents__page is-orange">14 - 15</span></li>
      <li class="contents__item"><span>Mission/Vision</span><span class="contents__page is-teal">16 - 17</span></li>
      <li class="contents__item"><span>A Place We Call Home</span><span class="contents__page is-orange">18</span></li>
      <li class="contents__item"><span>Memorials</span><span class="contents__page is-teal">19</span></li>
    </ol>
  </nav>

  <div class="brand-mark">
    <span class="brand-mark__dot"></span>
    <span class="brand-mark__name">Camp Thornbrook</span>
  </div>
</section>

<section class="page page--feature">
  <header class="feature-header">
    <h2 class="feature-header__title">Make the Difference</h2>
    <span class="feature-header__url">https://www.campthornbrook.org/</span>
  </header>
  <div class="feature-rule"></div>

  <div class="story story--left">
    <p>To say that 2020 has been a challenging year is a huge understatement! March 2020 is a month none of us will soon forget. Just as we were getting ready to ramp up for the summer, things began to shut down all around us. At first we hoped it would just be a few weeks only impacting our spring retreats, but as the spring progressed, it soon became evident our 2020 summer was being threatened.</p>
    <p>In late May, we made the difficult decision to cancel all summer events. For the first time in 73 years, there would be no summer camp at Thornbrook. Our summer programming is at the heart of what we do and who we are. From the very beginning, Thornbrook’s main mission has been to share Christ through the summer camp program.</p>
    <p>After dealing with the emotional aspect of not having camp this summer, we had to look at the reality of the financial impact canceling the summer would have on Thornbrook. Over 50% of our annual revenue comes from our summer programming and summer rentals. We also had to take into account the loss of our spring rentals and the possibility of fall rentals canceling. While we were confident God would provide for Thornbrook, as He always has, we weren’t sure how this would take place.</p>
    <p>We determined that even with drastically cutting expenses, we would need an additional $50,000 to make up for the lost revenue. In late June, we received a phone call from one of our long-time Thornbrook families who was interested in helping us through this difficult time. They generously pledged $10,000 as a matching gift to help motivate the Thornbrook family to give as well. In early July, we announced the “Make the Difference” fundraising campaign. Our initial goal was to raise $10,000 in one week to receive the matching gift with the hope of substantially reducing the $50,000 deficit.</p>
  </div>

  <div class="story story--right">
    <p>The Thornbrook family showed their love and dedication through their extraordinary generosity. By the end of Monday, the first day of the campaign, we had exceeded our initial goal of $10,000 ensuring the matching gift. By the end of the week, over $64,000 was raised! While 2020 has not been the year we had hoped for, it has been a year in which Thornbrook has been blessed beyond expectations!</p>
  </div>

  <div class="zigzag-band" role="img" aria-label="Teal zigzag divider ornament"></div>
  <div class="campaign-photo" role="img" aria-label="Make the Difference campaign poster, July 13th to 17th: a counselor hugging two young campers outdoors"></div>

  <div class="folio-bar"></div>
  <span class="folio">3</span>
</section>

</body>
</html>
```